Its time for a new website

We are at a point now where we are in desperate need of a new website. It was last updated 2006 but still looks like its 1995. We are looking for something eye catching to our clients but easy to navigate and add/remove photos of jobs/trucks and information. Our key business is the manufacture of fire appliances and resale of parts and equipment.

www.kestrelrigs.com.au

Coding

Coded - Design and coding required

Number of Pages Required

5+ page

Requirements
Must have
• Logo

```html
<!DOCTYPE html>
<html lang="en">
<head>
<meta charset="utf-8">
<title>Kestrel Rigs – Custom Firefighting Equipment</title>
<link rel="stylesheet" href="https://fonts.googleapis.com/css2?family=Oswald:wght@400;500&family=Open+Sans:wght@400;600&display=swap">
<style>
:root{
  --red:#e00b0b;
  --blue:#1a86d6;
  --ink:#222;
  --muted:#7a7a7a;
  --dark:#1f1513;
  --darker:#1a1210;
  --footer-text:#e8e2e0;
  --white:#fff;
}
*{box-sizing:border-box;margin:0;padding:0}
html,body{width:872px;height:1200px;overflow:hidden}
body{position:relative;background:var(--white);font-family:"Open Sans",sans-serif;color:var(--ink)}
.cond{font-family:"Oswald",sans-serif;letter-spacing:-.02em}
.abs{position:absolute}

/* header */
.site-header{position:absolute;left:0;top:0;width:872px;height:103px}
.brand{left:76px;top:24px;display:flex;align-items:center;gap:6px}
.brand-dot{width:14px;height:14px;border-radius:50%;background:var(--red)}
.brand-name{font-weight:600;font-size:15px;color:var(--blue)}
.call{left:554px;top:27px;font-size:11.5px;color:var(--ink)}
.new-btn{left:724px;top:18px;width:76px;height:32px;background:var(--red);color:var(--white);font-size:11.5px;display:flex;align-items:center;justify-content:center}
.main-nav{left:246px;top:69px;display:flex}
.main-nav a{font-family:"Oswald",sans-serif;font-size:11px;color:#444;text-decoration:none;margin-right:24px;letter-spacing:-.02em}
.main-nav a.active{color:#111;font-weight:500}

/* hero */
.hero{left:0;top:103px;width:872px;height:374px;background:radial-gradient(ellipse at 40% 60%,#c9a66a 0%,#7a5632 18%,#3a2a2a 45%,#221c24 75%,#14121a 100%)}
.hero-title{left:0;width:872px;top:126px;text-align:center;color:var(--white);font-size:28px;font-weight:500;line-height:1}
.hero-sub{left:0;width:872px;top:168px;text-align:center;color:var(--white);font-size:18px;font-weight:500}
.hero-btn{left:376px;top:207px;width:120px;height:32px;background:var(--red);color:var(--white);font-size:13.5px;display:flex;align-items:center;justify-content:center}
.hero-arrow{top:154px}
.job-band{left:0;top:477px;width:872px;height:43px;background:var(--red);display:flex;align-items:center;justify-content:center;gap:10px;color:var(--white);font-size:12.5px;font-weight:500}
.job-band .go{width:16px;height:16px;border-radius:50%;background:#222;display:flex;align-items:center;justify-content:center}

/* products */
.product{top:550px;width:232px}
.product .photo{width:224px;height:114px}
.product h2{font-family:"Oswald",sans-serif;font-weight:400;font-size:14px;color:var(--blue);margin:22px 0 14px;letter-spacing:-.02em}
.product p{font-size:9px;line-height:16.8px;color:var(--muted)}
.product .more{display:inline-flex;margin-top:14px;width:67px;height:30px;background:var(--red);color:var(--white);font-family:"Oswald",sans-serif;font-size:10.5px;align-items:center;justify-content:center}
.product.shifted .photo{margin-left:-6px}

/* footer */
.site-footer{left:0;top:831px;width:872px;height:309px;background:var(--dark)}
.col-title{font-family:"Oswald",sans-serif;font-size:14px;color:var(--blue);letter-spacing:-.02em}
.foot-text{font-size:9px;line-height:16.8px;color:var(--footer-text)}
.stamp{font-family:"Oswald",sans-serif;font-size:11px;color:var(--red);margin:2px 0 14px}
.view-more{font-family:"Oswald",sans-serif;font-size:10px;color:var(--footer-text)}
.round{width:26px;height:26px;border-radius:50%;background:#2e2624;border:1px solid #4a403d;display:flex;align-items:center;justify-content:center}
.works-photo{left:72px;top:912px;width:228px;height:176px;border:3px solid #3a2e2b;background:linear-gradient(180deg,#b8c3c6 0%,#9fa89a 40%,#b03030 55%,#8d2626 75%,#5f6a55 100%)}
.bottom-bar{left:0;top:1140px;width:872px;height:60px;background:var(--darker)}
.copy{left:74px;top:1164px;font-size:9px;color:#b9b0ad}
.social{left:624px;top:1157px;display:flex;gap:5px}
.social span{width:25px;height:25px;border-radius:50%;background:#3a3230}
</style>
</head>
<body>

<header class="site-header">
  <div class="abs brand"><span class="brand-dot"></span><span class="brand-name">Kestrel Rigs</span></div>
  <div class="abs call cond">CALL US: 08 9555 0142, 61 8 9555 0142</div>
  <div class="abs new-btn cond">NEW FOR 2015</div>
  <nav class="abs main-nav">
    <a class="active">HOME</a><a>ABOUT US</a><a>PUMPERS</a><a>TANKERS</a><a>GPA/RESUE</a><a>LIGHT TANKERS</a><a>TRAILERS</a><a>SLIP-ON UNITS</a><a>CONTACT US</a>
  </nav>
</header>

<section class="abs hero" role="img" aria-label="Welder at work with a shower of sparks">
  <div class="abs hero-title cond">KESTREL RIGS ARE WESTERN AUSTRALIA'S</div>
  <div class="abs hero-sub cond">LEADING MANUFACTURER OF CUSTOM FIREFIGHTING EQUIPMENT</div>
  <div class="abs hero-btn cond">2015 APPLIANCES</div>
  <svg class="abs hero-arrow" style="left:20px" width="28" height="60" viewBox="0 0 28 60"><polyline points="26,2 2,30 26,58" fill="none" stroke="#ddd" stroke-width="1.5"/></svg>
  <svg class="abs hero-arrow" style="left:822px" width="28" height="60" viewBox="0 0 28 60"><polyline points="2,2 26,30 2,58" fill="none" stroke="#ddd" stroke-width="1.5"/></svg>
</section>
<div class="abs job-band cond">CLICK HERE—EMPLOYMENT OPPORTUNITIES—CLICK HERE
  <span class="go"><svg width="8" height="8" viewBox="0 0 8 8"><polyline points="2,1 5,4 2,7" fill="none" stroke="#fff" stroke-width="1.4"/></svg></span>
</div>

<article class="abs product" style="left:72px">
  <div class="photo" role="img" aria-label="Red fire pumper truck parked on a park road" style="background:linear-gradient(180deg,#4f7a3a 0%,#3d6a2c 35%,#b01a1a 55%,#8a1414 80%,#6d6d6a 100%)"></div>
  <h2>PUMPERS</h2>
  <p>ur range of pumpers have been specifically designed for use in a broad range of areas such as metropolitan, industrial and mining applicationssuit.</p>
  <span class="more">READ MORE</span>
</article>
<article class="abs product shifted" style="left:330px">
  <div class="photo" role="img" aria-label="Silver tanker truck on a highway" style="background:linear-gradient(160deg,#6d7a55 0%,#8d8a7e 40%,#c9c9c6 55%,#6a6558 100%)"></div>
  <h2>TANKERS</h2>
  <p>ur range of pumpers have been specifically designed for use in a broad range of areas such as metropolitan, industrial and mining applicationssuit.</p>
  <span class="more">READ MORE</span>
</article>
<article class="abs product" style="left:576px">
  <div class="photo" role="img" aria-label="White semi truck on a desert road" style="background:linear-gradient(180deg,#a4784f 0%,#8a6a4a 45%,#e8e8e8 60%,#4a4a4a 100%)"></div>
  <h2>TRAILERS</h2>
  <p>ur range of pumpers have been specifically designed for use in a broad range of areas such as metropolitan, industrial and mining applicationssuit.</p>
  <span class="more">READ MORE</span>
</article>

<footer class="abs site-footer"></footer>
<div class="abs col-title" style="left:71px;top:868px">OUR WORKS</div>
<div class="abs round" style="left:246px;top:864px"><svg width="8" height="10" viewBox="0 0 8 10"><polyline points="6,1 2,5 6,9" fill="none" stroke="#fff" stroke-width="2"/></svg></div>
<div class="abs round" style="left:275px;top:864px"><svg width="8" height="10" viewBox="0 0 8 10"><polyline points="2,1 6,5 2,9" fill="none" stroke="#fff" stroke-width="2"/></svg></div>
<div class="abs works-photo" role="img" aria-label="Red fire tanker truck on a gravel yard"></div>

<div class="abs" style="left:368px;top:868px;width:240px">
  <div class="col-title" style="margin-bottom:14px">FOR ALL YOUR FIRE FIGHTING NEEDS</div>
  <p class="foot-text">A 7200 Litre Foam Tanker comprises of a Multi-baffled and internally lined Stainless Steel tank Based on a Harlan HT6 single-cab. Featured with a Huge Full Width</p>
  <div class="stamp">Last Update 10 April, 2006</div>
  <p class="foot-text" style="margin-top:12px">A 7200 Litre Foam Tanker comprises of a Multi-baffled and internally lined Stainless Steel tank Based.</p>
  <div class="stamp">Last Update 10 April, 2006</div>
  <div class="view-more">{View More}</div>
</div>

<div class="abs" style="left:647px;top:868px;width:162px">
  <div class="col-title" style="margin-bottom:14px">CONTACT US</div>
  <p class="foot-text">Kestrel Rigs manufacture quality fire truck and tender units in the South West region of Australia</p>
  <p class="foot-text" style="margin-top:16px">Lot 14 Banksia Road Wandering 6308<br>Western Australia<br>Phone 08 9555 0142 ------<br>Phone (International) +61 8 9555 0142<br>Fax 08 9555 0187 ------<br>Fax (International) +61 8 9555 0187<br>email Address</p>
</div>

<div class="abs bottom-bar"></div>
<div class="abs copy">© Copyright 2015 www.kestrelrigs.com.au &nbsp;All Rights Reserved &nbsp;| &nbsp;Sitemap</div>
<div class="abs social" aria-label="Social links"><span></span><span></span><span></span><span></span><span></span><span></span></div>

</body>
</html>
```